Business Cards - Brightpath Horizon

need to design unique business card for my mortgage business. I need to design credit card style business card for my business or any unique idea that you might have

Target Market(s)

Home Loan customers

Industry/Entity Type

Mortgage Brokerage

Contact Information for Business Card

please design credit card style or very unique style business card

Colors

Designer to choose colors to be used in the design.

Requirements
Must have
• Name
• position
• Phone number
• fax number
• email address
• website address
• social media address
• All above fields will be provided once design in finalised

```html
<!DOCTYPE html>
<html lang="en">
<head>
<meta charset="utf-8">
<title>Brightpath Horizon – Business Cards</title>
<link rel="stylesheet" href="https://fonts.googleapis.com/css2?family=Old+Standard+TT:wght@400;700&display=swap">
<style>
  :root {
    --page: #e9e6e1;
    --royal: #0330c4;
    --white: #ffffff;
    --orange: #fd8c14;
    --shadow: rgba(0, 0, 0, 0.35);
  }
  * { margin: 0; padding: 0; box-sizing: border-box; }
  html, body {
    width: 1200px; height: 960px; overflow: hidden;
    background: var(--page);
  }
  body { position: relative; font-family: "Old Standard TT", Georgia, serif; }

  .card {
    position: absolute;
    width: 600px; height: 342px;
    box-shadow: 2px 3px 5px var(--shadow);
    overflow: hidden;
  }
  .card--front { left: 314px; top: 113px; background: var(--royal); }
  .card--back  { left: 311px; top: 472px; background: var(--orange); }

  .roof { position: absolute; inset: 0; }

  .contact {
    position: absolute; right: 38px; top: 39px;
    text-align: right; color: var(--white);
  }
  .contact__name { font-size: 21px; letter-spacing: 0.5px; line-height: 26px; }
  .contact__role { font-size: 15px; letter-spacing: 0.4px; line-height: 20px; margin-bottom: 14px; }
  .contact__list { list-style: none; font-size: 13.5px; line-height: 19.5px; }
  .contact__list li { display: flex; justify-content: flex-end; align-items: center; gap: 7px; }
  .contact__list svg { width: 13px; height: 13px; fill: var(--white); }

  .brand {
    position: absolute; left: 40px; top: 218px;
    text-align: center; width: 220px;
  }
  .brand__name {
    font-size: 32px; line-height: 34px; letter-spacing: 1px;
    color: var(--royal); font-weight: 400; text-transform: uppercase;
  }

  .back-brand {
    position: absolute; left: 0; right: 0; top: 148px; text-align: center;
  }
  .back-brand .brand__name { color: var(--white); font-size: 40px; line-height: 42px; }

  .social {
    position: absolute; left: 0; right: 0; top: 280px;
    display: flex; justify-content: center; gap: 4px;
  }
  .social__dot { width: 26px; height: 26px; border-radius: 50%; background: var(--white); }
</style>
</head>
<body>

  <section class="card card--front">
    <svg class="roof" width="600" height="342" viewBox="0 0 600 342">
      <polygon points="0,133 129,42 600,342 0,342" fill="#ffffff"/>
      <g fill="#0330c4">
        <rect x="106" y="94" width="22" height="22"/>
        <rect x="132" y="94" width="22" height="22"/>
        <rect x="106" y="120" width="22" height="22"/>
        <rect x="132" y="120" width="22" height="22"/>
      </g>
    </svg>

    <div class="contact">
      <p class="contact__name">DANIEL ROWE</p>
      <p class="contact__role">CEO/FOUNDER</p>
      <ul class="contact__list">
        <li>555 214 7730
          <svg viewBox="0 0 16 16"><path d="M3 1l3 3-1.5 2c1 2 3 4 5 5L11.5 9.5l3 3-2 2.5C6 14 2 10 1 3z"/></svg></li>
        <li>555 214 7731
          <svg viewBox="0 0 16 16"><path d="M4 1h8v4H4zM1 6h14v6h-3v3H4v-3H1zM5 10v4h6v-4z"/></svg></li>
        <li>hello@brightpathhz.com
          <svg viewBox="0 0 16 16"><path d="M1 3h14v10H1zM2 4.5v.5l6 4 6-4v-.5zM2 6.2V12h12V6.2L8 10.2z"/></svg></li>
        <li>www.brightpathhz.com
          <svg viewBox="0 0 16 16"><circle cx="8" cy="8" r="7"/><path d="M5 4c2 1 1 3 3 3s1 3 3 3M9 3c1 1 3 1 3 3" stroke="#0330c4" stroke-width="1.4" fill="none"/></svg></li>
      </ul>
    </div>

    <div class="brand">
      <p class="brand__name">Brightpath<br>Horizon</p>
    </div>
  </section>

  <section class="card card--back">
    <div class="back-brand">
      <p class="brand__name">Brightpath Horizon</p>
    </div>
    <div class="social" role="img" aria-label="Social media links">
      <span class="social__dot"></span>
      <span class="social__dot"></span>
      <span class="social__dot"></span>
      <span class="social__dot"></span>
    </div>
  </section>

</body>
</html>
```